Business Card for beauty technology startup

Design Glimora Business Card for a Beauty, based on the website identity and colors (https://www.glimora-example.com).
Glimora is a beauty tech startup that gathers helpful product info for beauty lovers and consumers (such as availability on stores, price range and product reviews) for makeup products. The card design must be young, colorful but clean, and very modern.

Target Market(s)

woman, 15-35

Industry/Entity Type

Cosmetics

Contact Information for Business Card

Full Name, address, phone

Font styles to use
Other font styles liked:
• Advent Pro

Colors
e34297
86cfc6
ffffff
5c5c5c
e8e8e8
e667a6
b2b2b2

Requirements
Must have
• One full colored side with a creative design and another with card info
• Use Color palette: #95C5C5 and/or #D38AA5
• Use fonts: Advent Pro
• Use website identity: https://www.glimora-example.com
Nice to have
• If needed extra font: Roboto

```html
<!DOCTYPE html>
<html lang="en">
<head>
<meta charset="UTF-8">
<title>Glimora Business Card</title>
<link rel="stylesheet" href="https://fonts.googleapis.com/css2?family=Advent+Pro:wght@300;400&family=Roboto:wght@300;400;700&display=swap">
<style>
  :root {
    --page-bg: #efeaec;
    --mauve-light: #dfb5cf;
    --mauve: #b47b96;
    --mauve-deep: #a56e88;
    --white: #ffffff;
    --paper: #f4f4f4;
    --grey-arc: #b2b2b2;
    --card-shadow: rgba(60, 30, 45, 0.22);
  }
  * { box-sizing: border-box; margin: 0; padding: 0; }
  html, body {
    width: 1200px; height: 900px; overflow: hidden;
    background: var(--page-bg);
  }
  .canvas {
    position: relative; width: 1200px; height: 900px;
  }
  .card {
    position: absolute; width: 660px; height: 377px;
    overflow: hidden; border-radius: 4px;
    box-shadow: 0 14px 30px var(--card-shadow);
  }
  /* Front side */
  .card-front {
    left: 150px; top: 52px;
    background: linear-gradient(100deg, var(--mauve-light) 0%, var(--mauve) 55%, var(--mauve-deep) 100%);
    color: var(--white);
    display: flex; flex-direction: column; align-items: center; justify-content: center;
  }
  .brand-mark {
    width: 62px; height: 62px; border: 2px solid currentColor; border-radius: 50%;
    margin-bottom: 16px;
  }
  .brand-name {
    font-family: 'Advent Pro', sans-serif; font-weight: 300;
    font-size: 46px; letter-spacing: 10px; padding-left: 10px; line-height: 1;
  }
  .brand-web {
    font-family: 'Roboto', sans-serif; font-weight: 300;
    font-size: 13px; letter-spacing: 4px; margin-top: 22px; padding-left: 4px;
  }
  /* Back side */
  .card-back {
    left: 390px; top: 470px;
    background: linear-gradient(100deg, var(--mauve-light) 0%, var(--mauve) 50%, var(--mauve-deep) 100%);
  }
  .back-shapes { position: absolute; inset: 0; }
  .back-brand {
    position: absolute; left: 60px; top: 150px; width: 300px;
    display: flex; flex-direction: column; align-items: center;
    color: var(--mauve-deep);
  }
  .back-brand .brand-mark { width: 58px; height: 58px; margin-bottom: 14px; }
  .back-brand .brand-name { font-size: 44px; }
  .contact {
    position: absolute; right: 26px; top: 40px;
    text-align: right; color: var(--white);
    font-family: 'Roboto', sans-serif; font-weight: 300; font-size: 13px; line-height: 1.4;
  }
  .contact-name { font-weight: 700; font-size: 14px; letter-spacing: 0.5px; }
  .contact-role { margin-bottom: 22px; }
  .contact-address { margin-bottom: 10px; }
  .contact-line { display: flex; justify-content: flex-end; align-items: center; gap: 8px; }
  .contact-line svg { width: 11px; height: 11px; flex: none; }
</style>
</head>
<body>
<main class="canvas">

  <section class="card card-front" aria-label="Card front">
    <span class="brand-mark" aria-hidden="true"></span>
    <h1 class="brand-name">GLIMORA</h1>
    <p class="brand-web">www.glimora-example.com</p>
  </section>

  <section class="card card-back" aria-label="Card back">
    <svg class="back-shapes" viewBox="0 0 660 377" aria-hidden="true">
      <circle cx="205" cy="420" r="345" fill="var(--grey-arc)"/>
      <circle cx="170" cy="420" r="335" fill="var(--paper)"/>
    </svg>

    <div class="back-brand">
      <span class="brand-mark" aria-hidden="true"></span>
      <h2 class="brand-name">GLIMORA</h2>
    </div>

    <div class="contact">
      <p class="contact-name">LENA MARWICK</p>
      <p class="contact-role">CEO/FOUNDER</p>
      <p class="contact-address">4120 Willowbend Court<br>Fairmont, Oregon 97000</p>
      <p class="contact-line">555 014 2231
        <svg viewBox="0 0 12 12" fill="var(--white)"><path d="M2.5 1l2 2.5-1 1.2a7 7 0 0 0 3.8 3.8l1.2-1 2.5 2-1.2 1.5C5 10.5 1.5 7 1 2.2z"/></svg>
      </p>
      <p class="contact-line">555 017 6480
        <svg viewBox="0 0 12 12" fill="none" stroke="var(--white)" stroke-width="1.4"><rect x="3" y="1" width="6" height="10" rx="1"/></svg>
      </p>
      <p class="contact-line">555 019 3372
        <svg viewBox="0 0 12 12" fill="var(--white)"><rect x="1" y="4" width="10" height="6" rx="1"/><rect x="3" y="1" width="6" height="3"/></svg>
      </p>
      <p class="contact-line">hello@glimora-example.com
        <svg viewBox="0 0 12 12" fill="none" stroke="var(--white)" stroke-width="1.3"><rect x="1" y="2.5" width="10" height="7"/><path d="M1 2.5l5 4 5-4"/></svg>
      </p>
      <p class="contact-line">www.glimora-example.com
        <svg viewBox="0 0 12 12" fill="none" stroke="var(--white)" stroke-width="1.2"><circle cx="6" cy="6" r="5"/><path d="M1 6h10M6 1c-2.5 3-2.5 7 0 10M6 1c2.5 3 2.5 7 0 10"/></svg>
      </p>
    </div>
  </section>

</main>
</body>
</html>
```